Complete redesign of Licensed Medical Cannabis Dispensary website

Redesign website to modernize it and simplify it and add a self service reservation/preorder interactive delivery form. Also integrate current POS system that has current inventory. Here is a website for inspiration that I really like because of it simplicity https://www.leafroute.example and easy ordering option. Attached is our logo.... please design around that and this is our website address www.meadowcrestcourier.example

Font styles to use
Sans Serif

Colors
5c5c5c
cbcbcb
000000
add136

Requirements
Must have
• inventory thats integrated with pos
• online reservation/delivery form
Nice to have
• a website thats modern and simple
• The website designed are the logo that is attached
Should not have
• too much information

```html
<!DOCTYPE html>
<html lang="en">
<head>
<meta charset="utf-8">
<title>Meadowcrest – California's Medical Marijuana</title>
<link href="https://fonts.googleapis.com/css2?family=Oswald:wght@500;700&family=Open+Sans:wght@400;600;700&display=swap" rel="stylesheet">
<style>
:root{
  --green:#1f8a1f;
  --green-dark:#146b14;
  --lime:#add136;
  --text:#5c5c5c;
  --line:#cbcbcb;
  --black:#000000;
  --mint:#e4f6e0;
  --white:#ffffff;
}
*{box-sizing:border-box;margin:0;padding:0}
html,body{width:1200px;height:4147px;overflow:hidden}
body{font-family:"Open Sans",sans-serif;color:var(--text);background:var(--white);position:relative}
.abs{position:absolute}
.heading{font-family:"Oswald",sans-serif;font-weight:700;color:var(--green);text-transform:uppercase;text-align:center;font-size:40px;letter-spacing:.5px}
.heading-rule{width:90px;height:3px;background:var(--line);margin:12px auto 0}
.btn{display:inline-block;background:var(--lime);color:var(--white);font-weight:700;font-size:15px;border-radius:30px;padding:14px 36px}

/* header */
.site-header{top:0;left:0;width:1200px;height:150px}
.brand{left:100px;top:34px;display:flex;align-items:center;gap:16px}
.brand-dot{width:64px;height:64px;border-radius:50%;background:var(--green)}
.brand-name{font-size:34px;font-weight:600;color:var(--green)}
.contact{top:32px;display:flex;align-items:center;gap:14px;font-size:15px;color:var(--green);line-height:1.25}
.contact .ic{width:32px;height:32px;border-radius:50%;background:var(--green);display:flex;align-items:center;justify-content:center}
.nav{top:94px;left:515px;width:685px;height:51px;background:var(--green);clip-path:polygon(0 0,100% 0,100% 100%,30px 100%);display:flex;align-items:center;justify-content:flex-end;gap:50px;padding-right:50px;color:var(--white);font-weight:700;font-size:15px}

/* hero */
.hero{top:150px;left:0;width:1200px;height:445px;background:linear-gradient(90deg,#eefaea 0%,#dff5d9 100%)}
.hero-photo{left:730px;top:40px;width:440px;height:330px;border-radius:50% 40% 45% 50%;background:radial-gradient(circle at 50% 50%,#9bb64a 0%,#6f9a3a 45%,rgba(223,245,217,0) 72%)}
.hero-title{left:100px;top:104px;z-index:2;white-space:nowrap;font-family:"Oswald",sans-serif;font-weight:700;font-size:41px;color:var(--green);letter-spacing:.3px}
.hero-text{left:100px;top:178px;width:610px;z-index:2;font-size:23px;font-weight:700;color:var(--text);line-height:1.4}
.hero .btn{left:100px;top:268px;position:absolute;z-index:2}
.dots{left:576px;top:390px;display:flex;gap:6px}
.dots span{width:10px;height:10px;border-radius:50%;border:1.5px solid var(--text)}
.dots span:first-child{background:var(--text)}

/* steps */
.steps-head{top:700px;left:0;width:1200px}
.step{top:820px;width:200px;text-align:center}
.step-circle{width:200px;height:200px;border-radius:50%;background:linear-gradient(135deg,#4fae3a,#156d16);border:8px solid #7fc35c;box-shadow:0 6px 0 #3a3a3a;display:flex;align-items:center;justify-content:center}
.step-label{margin-top:24px;font-family:"Oswald",sans-serif;font-weight:500;font-size:22px;color:var(--black)}

/* banner */
.banner{top:1170px;left:0;width:1200px;height:373px}
.banner-bg{position:absolute;inset:0;background:linear-gradient(90deg,#3f7d2e 0%,#5b9a3d 45%,#2f6e27 100%)}
.banner-curve{position:absolute;left:0;bottom:-1px}
.banner-title{top:96px;left:0;width:1200px;text-align:center;font-family:"Oswald",sans-serif;font-weight:700;font-size:36px;color:var(--white)}
.banner-text{top:156px;left:150px;width:900px;text-align:center;font-size:22px;color:var(--white);line-height:1.4}
.btn-outline{top:250px;left:534px;width:132px;height:46px;border:2px solid var(--white);border-radius:25px;color:var(--white);font-weight:700;font-size:15px;display:flex;align-items:center;justify-content:center}

/* shop */
.shop-head{top:1640px;left:0;width:1200px}
.product{width:235px;text-align:center}
.product-photo{width:235px;height:222px;border:1px solid var(--line)}
.stars{margin-top:12px;color:#d9a400;font-size:17px;letter-spacing:2px}
.product-name{font-size:19px;color:var(--black);margin-top:4px}
.product-price{font-size:19px;font-weight:700;color:var(--green);margin-top:6px}
.shop-more{top:2510px;left:534px;position:absolute;padding:14px 34px}

/* reviews */
.reviews{top:2657px;left:0;width:1200px;height:429px;background:linear-gradient(90deg,#2f7a23,#3f9230 50%,#2f7a23)}
.quote-badge{left:555px;top:-46px;width:90px;height:90px;border-radius:50%;background:var(--white);display:flex;align-items:center;justify-content:center;font-family:"Oswald",sans-serif;font-size:50px;color:var(--green);line-height:1;padding-top:18px}
.reviews-title{top:68px;left:0;width:1200px;text-align:center;font-family:"Oswald",sans-serif;font-weight:700;font-size:38px;color:var(--white)}
.avatar{left:540px;top:130px;width:120px;height:120px;border-radius:50%;border:4px solid var(--white);background:linear-gradient(#c98f7a,#8e4b3b)}
.reviewer{top:262px;left:0;width:1200px;text-align:center;color:var(--white);font-size:22px}
.review-text{top:302px;left:260px;width:680px;text-align:center;color:var(--white);font-size:13px;line-height:1.75}
.arrow{top:270px}

/* forums */
.forums{top:3086px;left:0;width:1200px;height:818px;background:linear-gradient(#f4f6f4,#eef2ee)}
.forums-title{left:100px;top:108px;font-family:"Oswald",sans-serif;font-weight:700;font-size:40px;color:var(--green)}
.search{left:541px;top:116px;width:212px;height:38px;border:1.5px solid var(--text);border-radius:20px;font-size:12px;padding:10px 16px;display:flex;justify-content:space-between}
.forum-table{left:100px;top:212px;width:647px;border-collapse:collapse;font-size:13px}
.forum-table th{text-align:left;font-size:16px;font-weight:700;color:var(--black);padding:12px 0;border-top:1px solid var(--line);border-bottom:1px solid var(--line)}
.forum-table td{padding:16px 0;border-bottom:1px solid var(--line);vertical-align:top;color:var(--black)}
.forum-table .meta{color:var(--text);font-size:12px;margin-top:6px;display:flex;align-items:center;gap:8px}
.user-ic{width:16px;height:16px;border-radius:50%;background:var(--text);display:inline-block}
.panel{left:780px;width:265px;border:2px solid #6b6b6b;background:var(--white);padding:20px 22px}
.panel h3{font-weight:400;font-size:24px;color:#333;margin-bottom:14px}
.field-label{font-size:13px;color:#333;margin-top:6px}
.field{height:38px;background:#f0f0f0;margin:8px 0 12px}
.remember{font-size:11px;display:flex;align-items:center;gap:8px}
.remember i{width:14px;height:14px;border:1px solid var(--text)}
.panel .btn{margin-top:14px;padding:10px 26px;font-size:13px}
.topic-list li{list-style:none;font-size:12px;color:#333;padding:12px 0;border-bottom:1px solid var(--line);white-space:nowrap}

/* footer */
.site-footer{top:3904px;left:0;width:1200px;height:243px;background:linear-gradient(180deg,#a9da8c 0%,#d4efc3 100%)}
.footer-brand{left:100px;top:80px;display:flex;align-items:center;gap:16px}
.social{top:80px;width:56px;height:56px;border-radius:50%;background:var(--white)}
.copyright{top:200px;left:0;width:1200px;text-align:center;font-size:12px;color:#333}
</style>
</head>
<body>

<header class="site-header abs">
  <div class="brand abs"><span class="brand-dot"></span><span class="brand-name">Meadowcrest</span></div>
  <div class="contact abs" style="left:640px">
    <span class="ic"><svg width="16" height="12" viewBox="0 0 16 12"><rect x="0.5" y="0.5" width="15" height="11" fill="none" stroke="#fff"/><path d="M1 1l7 6 7-6" fill="none" stroke="#fff"/></svg></span>
    <div>Mail Us At<br>hello@meadowcrestcourier.example</div>
  </div>
  <div class="contact abs" style="left:944px">
    <span class="ic"><svg width="16" height="16" viewBox="0 0 24 24"><path fill="#fff" d="M6.6 10.8a15 15 0 006.6 6.6l2.2-2.2a1 1 0 011-.25 11.4 11.4 0 003.6.57 1 1 0 011 1V20a1 1 0 01-1 1A17 17 0 013 4a1 1 0 011-1h3.5a1 1 0 011 1c0 1.25.2 2.45.57 3.6a1 1 0 01-.25 1z"/></svg></span>
    <div>Call Us At<br>(+1) 555 014 2287</div>
  </div>
  <nav class="nav abs"><span>LOGIN / SIGN UP</span><span>CONTACT</span><span>FORUMS</span><span>ONLINE STORE ⊕</span></nav>
</header>

<section class="hero abs">
  <div class="hero-photo abs" role="img" aria-label="Cannabis leaf resting on dried flower buds"></div>
  <h1 class="hero-title abs">CALIFORNIA'S MEDICAL MARIJUANA</h1>
  <p class="hero-text abs">Lorem ipsum dolor sit amet, consectetur adipisc nam iaculis odio leo, ac maximus justo .</p>
  <span class="btn">Buy Now</span>
  <div class="dots abs"><span></span><span></span><span></span><span></span></div>
</section>

<section>
  <div class="steps-head abs"><h2 class="heading">How Its Work</h2><div class="heading-rule"></div></div>
  <div class="step abs" style="left:102px"><div class="step-circle"><svg width="64" height="74" viewBox="0 0 64 74" fill="none" stroke="#fff" stroke-width="4"><path d="M4 4h38l18 18v48H4z"/><path d="M42 4v18h18M16 36h32M16 48h32M16 60h24"/></svg></div><div class="step-label">Sign Up</div></div>
  <div class="step abs" style="left:367px"><div class="step-circle"><svg width="72" height="64" viewBox="0 0 72 64"><path d="M2 6h12l10 36h38l8-26H20" fill="none" stroke="#fff" stroke-width="5"/><circle cx="28" cy="54" r="6" fill="#fff"/><circle cx="58" cy="54" r="6" fill="#fff"/></svg></div><div class="step-label">Place Order</div></div>
  <div class="step abs" style="left:633px"><div class="step-circle"><svg width="76" height="56" viewBox="0 0 76 56" fill="none" stroke="#fff" stroke-width="5"><rect x="3" y="3" width="70" height="50"/><path d="M4 4l34 28 34-28"/></svg></div><div class="step-label">Get Confirmation</div></div>
  <div class="step abs" style="left:898px"><div class="step-circle"><svg width="64" height="70" viewBox="0 0 64 70"><path d="M20 20V14a12 12 0 0124 0v6" fill="none" stroke="#fff" stroke-width="5"/><path d="M6 20h52l4 48H2z" fill="#fff"/></svg></div><div class="step-label">Receive Delivery</div></div>
</section>

<section class="banner abs">
  <div class="banner-bg" role="img" aria-label="Close-up of green cannabis leaves"></div>
  <svg class="banner-curve" width="1200" height="90" viewBox="0 0 1200 90"><path d="M0 90V0Q600 110 1200 0V90z" fill="#fff"/></svg>
  <h2 class="banner-title abs">BUY LEGAL CALIFORNIA'S CANNABIS</h2>
  <p class="banner-text abs">Aliquam feugiat enim nec condimentum ultricies. Orci varius natoque penatibus et magnis dis parturient montes, nascetur ridiculus mus</p>
  <span class="btn-outline abs">Read More</span>
</section>

<section>
  <div class="shop-head abs"><h2 class="heading">Shop Now</h2><div class="heading-rule"></div></div>
  <div class="product abs" style="left:100px;top:1748px"><div class="product-photo" role="img" aria-label="Dried cannabis flower buds" style="background:linear-gradient(135deg,#8a8d3a,#c4b766)"></div><div class="stars">★★★★☆</div><div class="product-name">LoremIpsum is Simple</div><div class="product-price">$ 120.00</div></div>
  <div class="product abs" style="left:354px;top:1748px"><div class="product-photo" role="img" aria-label="Dried cannabis flower buds" style="background:linear-gradient(135deg,#9a9a4a,#c9c07a)"></div><div class="stars">★★★★☆</div><div class="product-name">LoremIpsum is Simple</div><div class="product-price">$ 180.00</div></div>
  <div class="product abs" style="left:608px;top:1748px"><div class="product-photo" role="img" aria-label="Cannabis buds in a glass jar" style="background:linear-gradient(135deg,#5a4a22,#b89a48)"></div><div class="stars">★★★★☆</div><div class="product-name">LoremIpsum is Simple</div><div class="product-price">$ 80.00</div></div>
  <div class="product abs" style="left:863px;top:1748px"><div class="product-photo" role="img" aria-label="Frosty green cannabis buds" style="background:linear-gradient(135deg,#4f6a3a,#9fae7a)"></div><div class="stars">★★★★☆</div><div class="product-name">LoremIpsum is Simple</div><div class="product-price">$ 40.00</div></div>
  <div class="product abs" style="left:100px;top:2126px"><div class="product-photo" role="img" aria-label="Cannabis oil cartridge" style="background:linear-gradient(135deg,#2a2a22,#b89a30)"></div><div class="stars">★★★★☆</div><div class="product-name">LoremIpsum is Simple</div><div class="product-price">$ 120.00</div></div>
  <div class="product abs" style="left:354px;top:2126px"><div class="product-photo" role="img" aria-label="Amber concentrate in a jar" style="background:linear-gradient(135deg,#3a3020,#d8a020)"></div><div class="stars">★★★★☆</div><div class="product-name">LoremIpsum is Simple</div><div class="product-price">$ 180.00</div></div>
  <div class="product abs" style="left:608px;top:2126px"><div class="product-photo" role="img" aria-label="Labelled concentrate container" style="background:linear-gradient(135deg,#4a4a40,#a09060)"></div><div class="stars">★★★★☆</div><div class="product-name">LoremIpsum is Simple</div><div class="product-price">$ 80.00</div></div>
  <div class="product abs" style="left:863px;top:2126px"><div class="product-photo" role="img" aria-label="Golden wax concentrate" style="background:linear-gradient(135deg,#c98a10,#e8c040)"></div><div class="stars">★★★★☆</div><div class="product-name">LoremIpsum is Simple</div><div class="product-price">$ 40.00</div></div>
  <span class="btn shop-more">Read More</span>
</section>

<section class="reviews abs">
  <div class="quote-badge abs">❝</div>
  <h2 class="reviews-title abs">PRODUCT REVIEWS</h2>
  <div class="avatar abs" role="img" aria-label="Reviewer portrait"></div>
  <div class="reviewer abs">Sam Rowe</div>
  <p class="review-text abs">" Sed cursus purus pharetra condimentum fermentum. Maecenas non libero id odio fringilla luctus. Pellentesque habitant morbi tristique senectus et netus et malesuada fames ac turpis egestas. Sed luctus ultrices tincidunt dis. Pet lentesque feugiat felis in exercitem. "</p>
  <svg class="arrow abs" style="left:78px" width="20" height="30" viewBox="0 0 20 30"><path d="M16 2L4 15l12 13" fill="none" stroke="#fff" stroke-width="3"/></svg>
  <svg class="arrow abs" style="left:1104px" width="20" height="30" viewBox="0 0 20 30"><path d="M4 2l12 13L4 28" fill="none" stroke="#fff" stroke-width="3"/></svg>
</section>

<section class="forums abs">
  <h2 class="forums-title abs">FORUMS</h2>
  <div class="search abs"><span>Search The Forum...</span><span>⌕</span></div>
  <table class="forum-table abs">
    <thead><tr><th style="width:348px">Topics</th><th style="width:66px">Voices</th><th style="width:67px">Posts</th><th>Freshness</th></tr></thead>
    <tbody>
      <tr><td>Orci varius natoque penatibus et magnis<div class="meta">Started by: <span class="user-ic"></span> Sam Rowe</div></td><td>2</td><td>4</td><td>2 Months ago<div class="meta"><span class="user-ic"></span> Admin</div></td></tr>
      <tr><td>Fusce efficitur libero vitae massa varius<div class="meta">Started by: <span class="user-ic"></span> Sam Rowe</div></td><td>2</td><td>7</td><td>6 Months ago<div class="meta"><span class="user-ic"></span> Admin</div></td></tr>
      <tr><td>Suspendisse dignissim mi eros vel maximus<div class="meta">Started by: <span class="user-ic"></span> Sam Rowe</div></td><td>2</td><td>5</td><td>1 Years ago<div class="meta"><span class="user-ic"></span> Admin</div></td></tr>
      <tr><td>Viverra purus malesuada luctus condimeum<div class="meta">Started by: <span class="user-ic"></span> Sam Rowe</div></td><td>2</td><td>8</td><td>2 Years ago<div class="meta"><span class="user-ic"></span> Admin</div></td></tr>
      <tr><td>Phasellus dictum leo eget varius pretium<div class="meta">Started by: <span class="user-ic"></span> Sam Rowe</div></td><td>2</td><td>6</td><td>2 Years ago<div class="meta"><span class="user-ic"></span> Admin</div></td></tr>
    </tbody>
  </table>
  <aside class="panel abs" style="top:118px;height:320px">
    <h3>Register Now</h3>
    <div class="field-label">User Name</div><div class="field"></div>
    <div class="field-label">Password</div><div class="field"></div>
    <div class="remember"><i></i>Remember Me</div>
    <span class="btn">Submit</span>
  </aside>
  <aside class="panel abs" style="top:470px;height:251px">
    <h3 style="margin-bottom:4px">Recent Topics</h3>
    <ul class="topic-list">
      <li>Lorem Ipsum is Simple neque</li>
      <li>Vivamus eget posuere</li>
      <li>Sed cursus purus pharetra</li>
      <li style="border:0">Maecenas non libero id odio fringilla</li>
    </ul>
  </aside>
</section>

<footer class="site-footer abs">
  <div class="footer-brand abs"><span class="brand-dot"></span><span class="brand-name">Meadowcrest</span></div>
  <span class="social abs" style="left:904px" aria-label="Social link"></span>
  <span class="social abs" style="left:978px" aria-label="Social link"></span>
  <span class="social abs" style="left:1048px" aria-label="Social link"></span>
  <p class="copyright abs">Copyright© 2018. All Rights Reserved.</p>
</footer>

</body>
</html>
```